Business Card Design Project

After recently finishing a design project for the company logo using markbazaar, it's now time for a business card. Attached to this is the logo.

The requirements for the business card are pretty straightforward:

- A clean, uncomplicated look
- Consistent usage of fonts
- Designs for both single sided and double sided cards
- A modern layout with preferably space to refer to social media accounts and/or downloadable vcards through a qr code
- consistent application of the company colour scheme: red/white. Hex codes for exact colour can be provided

Thanks!

```html
<!DOCTYPE html>
<html lang="en">
<head>
<meta charset="utf-8">
<title>Kiln Row Recruiting – Business Card</title>
<link rel="stylesheet" href="https://fonts.googleapis.com/css2?family=Source+Sans+3:wght@400;600;700&display=swap">
<style>
  :root {
    --backdrop: #d9d1c7;
    --card: #231f20;
    --brand-red: #e31e24;
    --text-light: #ffffff;
    --card-shadow: rgba(0, 0, 0, 0.35);
  }
  * { margin: 0; padding: 0; box-sizing: border-box; }
  html, body {
    width: 960px;
    height: 1200px;
    overflow: hidden;
    background: var(--backdrop);
    font-family: "Source Sans 3", "Myriad Pro", Arial, sans-serif;
    color: var(--text-light);
  }
  .canvas { position: relative; width: 960px; height: 1200px; }
  .card {
    position: absolute;
    left: 55px;
    width: 840px;
    height: 480px;
    background: var(--card);
    border-radius: 28px;
    box-shadow: 0 6px 14px var(--card-shadow);
  }
  .card--front { top: 88px; }
  .card--back { top: 638px; }

  .wordmark {
    position: absolute;
    left: 140px;
    top: 72px;
    display: flex;
    align-items: center;
    gap: 28px;
  }
  .wordmark__square {
    width: 110px;
    height: 110px;
    background: var(--brand-red);
  }
  .wordmark__name {
    font-weight: 600;
    color: var(--text-light);
    line-height: 1;
  }
  .wordmark__primary { display: block; font-size: 82px; letter-spacing: -1px; }
  .wordmark__secondary { display: block; font-size: 44px; letter-spacing: 14px; margin-top: 8px; }

  .holder {
    position: absolute;
    right: 29px;
    top: 306px;
    text-align: right;
  }
  .holder__name { font-size: 25px; font-weight: 700; line-height: 32px; }
  .holder__role { font-size: 20px; font-weight: 400; line-height: 28px; }

  .contact { position: absolute; font-size: 20px; line-height: 28px; }
  .contact--address { left: 36px; top: 408px; }
  .contact--online { left: 328px; top: 400px; }
  .contact--phone { right: 29px; top: 400px; }
  .contact__line { display: flex; align-items: center; gap: 8px; white-space: nowrap; }
  .contact__line + .contact__line { margin-top: 7px; }
  .contact__icon { width: 16px; height: 16px; flex: none; fill: var(--text-light); }

  .back-mark {
    position: absolute;
    left: 340px;
    top: 160px;
    width: 160px;
    height: 160px;
    background: var(--brand-red);
  }
</style>
</head>
<body>
<main class="canvas">
  <section class="card card--front" aria-label="Card front">
    <div class="wordmark">
      <span class="wordmark__square" aria-hidden="true"></span>
      <h1 class="wordmark__name">
        <span class="wordmark__primary">Kiln Row</span>
        <span class="wordmark__secondary">RECRUITING</span>
      </h1>
    </div>

    <div class="holder">
      <p class="holder__name">Your Name</p>
      <p class="holder__role">Designation</p>
    </div>

    <address class="contact contact--address" style="font-style:normal">
      <p>1234, Street Name</p>
      <p>District, City, Country Code.</p>
    </address>

    <div class="contact contact--online">
      <p class="contact__line">
        <svg class="contact__icon" viewBox="0 0 16 16" aria-hidden="true"><path d="M1 3h14v10H1z M2 4v1l6 4 6-4V4z" fill-rule="evenodd"/></svg>
        info@yourwebsite.com
      </p>
      <p class="contact__line">
        <svg class="contact__icon" viewBox="0 0 16 16" aria-hidden="true"><circle cx="8" cy="8" r="6"/></svg>
        www.kilnrowhire.com
      </p>
    </div>

    <div class="contact contact--phone">
      <p class="contact__line">
        <svg class="contact__icon" viewBox="0 0 16 16" aria-hidden="true"><path d="M1 5c0-2 3-3 7-3s7 1 7 3v1h-4V5H5v1H1z M3 8l2-2h6l2 2v5H3z"/></svg>
        123-123-1234
      </p>
    </div>
  </section>

  <section class="card card--back" aria-label="Card back">
    <span class="back-mark" aria-hidden="true"></span>
  </section>
</main>
</body>
</html>
```